Veltra Cosmi Holdings Limited is a asset management company and project funding company, we specialise in high end finance for high net worth individuals, we are looking for a new logo letterhead template, email footer template and business card design. The letterhead template should be designed in word format so that the letterheading can be used electronically.

Below is the current logo that is a but plain and a little cheaper looking, colour schemes are not important just that it looks professional.

I am looking for a sharp impact that stands out,

Target Market(s)

High net worth individuals and institutions

Industry/Entity Type

Finance

Contact Information for Business Card

Veltra Cosmi Holdings Limited
T: 0333 418 2965

M: 07631 490718
E:derek.holm@veltra-cosmiholdings.com

REEDWATER COVE, EAST HARBOUR ROAD
FIFTH FLOOR, SUITE 512
P.O. BOX CB-47316
NASSAU BAHAMAS

Logo Text

Font styles to use
Serif
Sans Serif
Script
Other font styles liked:
• Tahoma

Colors
fbed22
6b449b
ec1f27
f78f20
33b8a4
0592cd

Requirements
Must have
• Colours schemes would look good in blue’s green’s purples.

Yellow and Purple together maybe a nice combination.
Nice to have
• I want the log to look sharpe, relate to a global presence, but I also want to it to look established.
Should not have
• N/a

```html
<!DOCTYPE html>
<html lang="en">
<head>
<meta charset="utf-8">
<title>Veltra Cosmi Holdings Limited — Business Card</title>
<link rel="stylesheet" href="https://fonts.googleapis.com/css2?family=Montserrat:wght@500;600;700&family=Roboto:wght@400&display=swap">
<style>
  :root {
    --navy: #0b2447;
    --navy-deep: #081d3b;
    --card-navy: #0d2a52;
    --paper: #f6f6f4;
    --gold: #e8a317;
    --ink: #0f2547;
    --white: #ffffff;
  }
  * { box-sizing: border-box; margin: 0; padding: 0; }
  html, body {
    width: 1200px; height: 800px; overflow: hidden;
    background: var(--navy-deep);
    font-family: "Montserrat", sans-serif;
  }
  .stage {
    position: relative; width: 1200px; height: 800px;
    background: radial-gradient(ellipse at 50% 45%, var(--navy) 0%, var(--navy-deep) 75%);
    display: flex; align-items: center; justify-content: center; gap: 60px;
  }
  .card {
    position: relative; width: 520px; height: 300px;
    box-shadow: 0 18px 40px rgba(0,0,0,0.35);
  }
  .card--front { background: var(--paper); color: var(--ink); }
  .card--back { background: var(--card-navy); color: var(--white); }

  .brand {
    display: flex; align-items: center; gap: 10px;
    font-weight: 700; text-transform: uppercase; line-height: 1.15;
  }
  .brand__mark { width: 14px; height: 14px; }
  .card--front .brand {
    position: absolute; top: 34px; right: 34px;
    font-size: 15px; letter-spacing: 1.5px; color: var(--ink);
  }
  .card--front .brand__mark { background: var(--gold); }

  .person { position: absolute; left: 34px; bottom: 30px; }
  .person__name { font-size: 21px; font-weight: 700; letter-spacing: 1px; color: var(--ink); }
  .person__role { font-size: 11px; font-weight: 600; letter-spacing: 1.5px; color: var(--gold); margin-bottom: 12px; }
  .contact { list-style: none; font-size: 11px; font-weight: 500; }
  .contact li { display: flex; align-items: center; gap: 8px; margin-bottom: 5px; }
  .contact svg { width: 14px; height: 14px; flex: none; }
  .address {
    margin-top: 8px; font-size: 9px; font-weight: 600; letter-spacing: 0.6px; line-height: 1.5;
    text-transform: uppercase;
  }

  .card--back .brand {
    position: absolute; top: 112px; left: 0; right: 0; justify-content: center;
    font-size: 22px; letter-spacing: 3px; color: var(--white);
  }
  .card--back .brand__mark { border: 2px solid var(--white); }
  .website {
    position: absolute; bottom: 40px; left: 0; right: 0; text-align: center;
    font-family: "Roboto", sans-serif; font-size: 13px; letter-spacing: 0.5px; color: var(--white);
  }
</style>
</head>
<body>
<main class="stage">
  <section class="card card--front" aria-label="Business card front">
    <div class="brand"><span class="brand__mark"></span><span>Veltra Cosmi<br>Holdings Limited</span></div>
    <div class="person">
      <h1 class="person__name">DEREK HOLM</h1>
      <p class="person__role">MANAGING DIRECTOR</p>
      <ul class="contact">
        <li>
          <svg viewBox="0 0 14 14" aria-hidden="true"><circle cx="7" cy="7" r="7" fill="#e8a317"/><path d="M4.5 3.8l1.3-.3.8 1.8-.9.6a4.5 4.5 0 0 0 2.4 2.4l.6-.9 1.8.8-.3 1.3c-3.3.1-5.8-2.4-5.7-5.7z" fill="#fff"/></svg>
          0333 418 2965
        </li>
        <li>
          <svg viewBox="0 0 14 14" aria-hidden="true"><circle cx="7" cy="7" r="7" fill="#e8a317"/><rect x="3.5" y="4.5" width="7" height="5" rx="0.6" fill="#fff"/><path d="M3.7 4.8L7 7.3l3.3-2.5" stroke="#e8a317" stroke-width="0.8" fill="none"/></svg>
          07631 490718
        </li>
        <li>
          <svg viewBox="0 0 14 14" aria-hidden="true"><circle cx="7" cy="7" r="7" fill="#e8a317"/><path d="M5.6 8.4l2.8-2.8M6.2 4.8l.9-.9a1.6 1.6 0 0 1 2.3 2.3l-.9.9M7.8 9.2l-.9.9a1.6 1.6 0 0 1-2.3-2.3l.9-.9" stroke="#fff" stroke-width="1" fill="none" stroke-linecap="round"/></svg>
          derek.holm@veltra-cosmiholdings.com
        </li>
      </ul>
      <p class="address">Reedwater Cove, East Harbour Road<br>Fifth Floor, Suite 512<br>P.O. Box CB-47316<br>Nassau Bahamas</p>
    </div>
  </section>

  <section class="card card--back" aria-label="Business card back">
    <div class="brand"><span class="brand__mark"></span><span>Veltra Cosmi<br>Holdings Limited</span></div>
    <p class="website">www.veltra-cosmiholdings.com</p>
  </section>
</main>
</body>
</html>
```